Redesign of luchtvoorraadpunt.nl – Clean, Trustworthy & User-Friendly Medical Equipment We...

PLEASE DO NOT CONTACT US OUTSIDE KRAVELPOINT.COM

We are looking for a talented and creative web designer to redesign the website www.luchtvoorraadpunt.nl, a Dutch online store specializing in medical oxygen concentrators and related products.

The current website is functional but outdated in terms of design, structure, and user experience. We want a fresh, modern, and trustworthy design that reflects the medical and professional nature of the business, while also being clear, accessible, and easy to navigate for a broad audience — including elderly users and people with limited technical skills.

About the Business:
Luchtvoorraadpunt.nl provides high-quality oxygen concentrators and accessories for both home and mobile use. The target audience includes individuals with respiratory conditions, healthcare professionals, and caregivers. Trust, clarity, and ease of use are key.

What We’re Looking For:
A clean and modern layout with a medical/professional feel
Strong focus on usability and accessibility
A design that works flawlessly on desktop and mobile (responsive)
Clear product presentation and easy-to-use navigation
Use of calming colors (e.g. white, light blue, grey tones) that reflect a medical/healthcare environment
Clear call-to-actions (e.g. “Vraag een offerte aan”, “Neem contact op”, etc.)
A design that builds trust and encourages inquiries or purchases

Pages We Need Designed:
Homepage
Product overview page (category)
Product detail page

Inspiration / Style Examples:
We’re looking for something in the style of:

Varnoth Healthcare
Bralto.nl
Welzijnsdepot.nl
Quenby (for clean layout and spacing)

Deliverables:
Full desktop and mobile designs (Figma, Adobe PS)
All source files and assets used (fonts, icons, images, etc.)
Clean and organized layers
Design must be ready for implementation by our development team

Target Market(s)

Luchtvoorraadpunt.nl targets both B2C and B2B audiences within the medical and healthcare sector in europe

Industry/Entity Type

Medical

Number of Pages Required

2 page

Font styles to use
Sans Serif

Requirements
Must have
• Clean and professional design, responsive layout (desktop and mobile), calming medical color scheme (e.g. light blue, white, grey), clear product presentation with specs and images, strong call-to-actions (e.g. "Vraag een offerte aan"), trust elements (certifications, reviews, support info), easy navigation for elderly and non-tech-savvy users, contact form easily accessible, SEO-friendly structure, fast loading design, privacy and regulatory compliance elements (e.g. CE mark info, medical disclaimers).
Should not have
• Overly complex design, dark or aggressive color schemes, small or hard-to-read fonts, cluttered layout, distracting animations, unnecessary pop-ups, autoplay videos or sounds, technical jargon without explanation, hidden contact options, slow-loading pages.

```html
<!DOCTYPE html>
<html lang="de">
<head>
<meta charset="utf-8">
<title>Luvra – Unsere Produkte</title>
<link href="https://fonts.googleapis.com/css2?family=Inter:wght@400;500;600;700&family=Lexend:wght@600;700&display=swap" rel="stylesheet">
<style>
:root{
  --blue:#0a6cb5;
  --blue-dark:#0b2a5c;
  --orange:#f26a1b;
  --sky:#7fc5ef;
  --sky-pale:#e7f3fb;
  --line:#e2e8ef;
  --text:#1f2b3a;
  --muted:#4a5563;
}
*{box-sizing:border-box;margin:0;padding:0}
html,body{width:1200px;height:2449px;overflow:hidden}
body{font-family:"Inter",sans-serif;color:var(--text);background:#fff;position:relative}
.wrap{position:absolute;left:141px;width:917px}
.ico{width:18px;height:18px;stroke:var(--orange);fill:none;stroke-width:1.6}

.topbar{top:0;height:39px;display:flex;align-items:center;justify-content:space-between;font-size:13px;border-bottom:1px solid var(--line)}
.topbar .grp{display:flex;gap:14px;align-items:center}
.topbar span{display:flex;align-items:center;gap:6px}
.flag{width:18px;height:12px;background:linear-gradient(#000 33%,#d00 33% 66%,#fc0 66%)}

.header{top:39px;height:68px;display:flex;align-items:center;justify-content:space-between}
.brand{font-family:"Lexend",sans-serif;font-weight:700;font-size:40px;color:var(--blue);letter-spacing:1px;display:flex;align-items:center;gap:6px}
.brand i{width:14px;height:14px;background:var(--orange);border-radius:50%;display:inline-block}
.hactions{display:flex;align-items:center;gap:26px;font-size:14px}
.hactions span{display:flex;gap:8px;align-items:center}
.cart{width:33px;height:33px;background:var(--orange);border-radius:5px;display:grid;place-items:center}

.nav{position:absolute;top:107px;left:0;width:1200px;height:35px;background:var(--blue)}
.nav ul{position:absolute;left:141px;width:917px;height:35px;display:flex;justify-content:space-between;align-items:center;list-style:none;font-size:13.5px;color:#fff}
.nav li.active{color:#9fd3f5}

.hero{position:absolute;top:142px;left:0;width:1200px;height:330px;background:linear-gradient(100deg,#6f6a60 0%,#3e4a56 30%,#56646f 55%,#9a8f7d 80%,#b9ab94 100%)}
.hero::after{content:"";position:absolute;inset:0;background:rgba(20,30,45,.35)}
.hero-cut{position:absolute;left:0;bottom:-1px;width:1200px;height:120px;z-index:2}
.hero-text{position:absolute;top:92px;left:0;width:1200px;text-align:center;z-index:3}
.hero-text h1{font-family:"Lexend",sans-serif;font-size:33px;color:#fff;font-weight:700}
.btn-orange{display:inline-block;margin-top:16px;background:var(--orange);color:#fff;font-size:13.5px;font-weight:500;padding:11px 20px;border-radius:4px}

.sec-title{position:absolute;top:488px;left:0;width:1200px;text-align:center}
.sec-title small{color:#6bb6e6;font-size:13px;display:inline-flex;align-items:center;gap:10px}
.sec-title small::before,.sec-title small::after{content:"";width:18px;height:1px;background:#6bb6e6}
.sec-title h2{font-family:"Lexend",sans-serif;font-size:30px;color:var(--blue);margin-top:4px;font-weight:700}
.sec-title h2 em{font-style:normal;color:var(--orange)}

.sidebar{position:absolute;left:141px;top:573px;width:206px;height:1209px;background:var(--sky-pale);border:1px solid #cfe3f2;border-radius:3px;padding:0 8px;font-size:12px}
.sb-head{display:flex;justify-content:space-between;align-items:center;height:36px;border-bottom:1px solid #c9dcea;font-weight:600;font-size:13px}
.clear{font-size:11px;font-weight:400;background:#fff;border:1px solid var(--line);padding:2px 6px;color:var(--muted)}
.clear b{color:#e23;font-weight:400}
.sb-sec{border-bottom:1px solid #c9dcea;padding-bottom:14px}
.sb-title{display:flex;justify-content:space-between;align-items:center;height:40px;font-weight:600;font-size:13px}
.minus{width:14px;height:14px;border:1.3px solid var(--blue);border-radius:50%;position:relative}
.minus::after{content:"";position:absolute;left:3px;right:3px;top:5.5px;height:1.3px;background:var(--blue)}
.range{position:relative;height:14px;margin:0 4px}
.range::before{content:"";position:absolute;left:0;right:0;top:6px;height:2px;background:var(--blue)}
.range i{position:absolute;top:2px;width:10px;height:10px;border-radius:50%;background:var(--blue)}
.prices{display:flex;align-items:center;gap:6px;margin-top:8px}
.prices span{width:70px;height:26px;background:#fff;border:1px solid var(--line);display:grid;place-items:center;font-size:11px;color:var(--muted)}
.brands{display:grid;grid-template-columns:repeat(3,60px);gap:5px 5px}
.brands span{height:26px;background:#fff;border:1px solid var(--line);display:grid;place-items:center;font-size:11px;font-weight:600;color:var(--blue)}
.tags{list-style:none;margin-top:4px;position:relative}
.tags li{display:flex;align-items:center;gap:6px;height:25px;color:#3a4452}
.tags li::before{content:"";width:9px;height:9px;border:1px solid #b8c4cf;background:#fff}
.tags::after{content:"";position:absolute;right:2px;top:0;width:3px;height:264px;background:#bfd9ec}
.tags .thumb{position:absolute;right:2px;top:42px;width:3px;height:26px;background:var(--blue);z-index:1}

.toolbar{position:absolute;left:375px;top:573px;width:683px;height:44px;background:#f3f6f9;border:1px solid var(--line);display:flex;align-items:center;padding:0 8px 0 12px;font-size:12px}
.view{display:flex;gap:6px;color:var(--blue);align-items:center}
.compare{display:flex;align-items:center;gap:6px;margin-left:14px;margin-right:auto}
.tb-btn{background:var(--blue);color:#fff;padding:8px 11px;font-size:12px;border-radius:2px}
.tb-sel{height:29px;background:#fff;border:1px solid #d6dde4;display:flex;align-items:center;justify-content:space-between;padding:0 8px;color:var(--muted);margin:0 8px}

.grid{position:absolute;left:376px;top:630px;display:grid;grid-template-columns:repeat(3,211px);grid-auto-rows:368px;column-gap:24px;row-gap:23px}
.card{border:1px solid var(--line);border-radius:6px;padding:6px;text-align:center}
.photo{height:240px;border-radius:2px;background:linear-gradient(#82c6ee 0 73%,#fff 73%)}
.photo.alt{background:linear-gradient(#dcecf7 0 73%,#fff 73%)}
.card h3{font-weight:500;font-size:16px;color:var(--blue);line-height:23px;margin-top:18px}
.price{font-size:19px;font-weight:500;margin-top:2px}
.stars{display:flex;justify-content:center;gap:6px;margin-top:8px}
.stars svg{width:16px;height:16px;fill:#f58a07}

.pager{position:absolute;top:1811px;left:545px;display:flex;gap:7px}
.pager span{width:28px;height:28px;border:1px solid #cfd6dd;display:grid;place-items:center;font-size:12px}
.pager .prev{background:var(--blue);border-color:var(--blue)}
.pager .next{background:var(--orange);border-color:var(--orange)}

.pay-band{position:absolute;top:2002px;left:0;width:1200px;height:394px;background:var(--sky-pale)}
.pay{position:absolute;left:141px;top:1897px;width:917px;height:208px;background:var(--sky);border-radius:8px;text-align:center}
.pay h2{font-family:"Lexend",sans-serif;font-size:29px;color:var(--blue-dark);margin-top:38px;font-weight:700}
.pay h2 em{font-style:normal;color:var(--orange)}
.cards{display:flex;justify-content:center;gap:15px;margin-top:14px}
.cards span{width:97px;height:60px;background:#fff;border-radius:4px;box-shadow:0 3px 6px rgba(0,0,0,.18);display:grid;place-items:center;font-size:14px;font-weight:700;color:var(--blue-dark)}

.footer{position:absolute;top:2160px;left:143px;display:flex;font-size:13px;color:var(--text)}
.fcol{position:relative}
.fcol h4{font-size:18px;font-weight:500;color:var(--blue-dark);padding-top:12px}
.fcol h4::before{content:"";position:absolute;margin-top:-12px;width:18px;height:2px;background:#8cc7ee}
.fcol ul{list-style:none;margin-top:12px}
.fcol li{height:28px}
.fcol li::before{content:"» ";}
.finfo{display:flex;gap:10px;margin-top:12px;font-size:13px;line-height:19px}
.finfo b{font-weight:600;color:var(--blue-dark)}
.bottom{position:absolute;top:2396px;left:0;width:1200px;height:53px;background:var(--blue-dark);color:#fff;font-size:13px;display:grid;place-items:center}
</style>
</head>
<body>
<svg width="0" height="0" style="position:absolute"><defs><symbol id="star" viewBox="0 0 24 24"><path d="M12 2l3 6.6 7.2.8-5.4 4.9 1.5 7.1L12 17.8 5.7 21.4l1.5-7.1L1.8 9.4 9 8.6z"/></symbol></defs></svg>

<div class="wrap topbar">
  <div class="grp">
    <span><svg class="ico" viewBox="0 0 24 24"><path d="M12 20s-8-5-8-11a4.5 4.5 0 0 1 8-2.8A4.5 4.5 0 0 1 20 9c0 6-8 11-8 11z"/></svg>Wish list</span>
    <span><svg class="ico" viewBox="0 0 24 24"><path d="M4 7h13l-3-3M20 17H7l3 3"/></svg>Compare</span>
  </div>
  <div class="grp">
    <span><svg class="ico" viewBox="0 0 24 24"><path d="M2 6h12v10H2zM14 10h4l3 3v3h-7M6 18a2 2 0 1 0 0 .1M17 18a2 2 0 1 0 0 .1"/></svg>Dispatch</span>
    <span><svg class="ico" viewBox="0 0 24 24"><path d="M3 11h8v9H3zM13 11h8v9h-8zM8 3h8v8H8z"/></svg>Stock</span>
    <span>Deut <i class="flag"></i> ▾</span>
  </div>
</div>

<div class="wrap header">
  <div class="brand"><i></i>luvra</div>
  <div class="hactions">
    <span><svg class="ico" viewBox="0 0 24 24"><path d="M5 3h4l2 5-3 2a11 11 0 0 0 6 6l2-3 5 2v4a2 2 0 0 1-2 2A17 17 0 0 1 3 5a2 2 0 0 1 2-2z"/></svg>070-1234567</span>
    <span>Login</span>
    <span>Register</span>
    <svg class="ico" style="width:20px;height:20px" viewBox="0 0 24 24"><circle cx="10" cy="10" r="6"/><path d="M15 15l5 5"/></svg>
    <span class="cart"><svg class="ico" style="stroke:#fff" viewBox="0 0 24 24"><path d="M3 4h3l2 11h11l2-8H7M9 20a1 1 0 1 0 0 .1M18 20a1 1 0 1 0 0 .1"/></svg></span>
  </div>
</div>

<nav class="nav"><ul>
  <li class="active">Home</li><li>Over ons</li><li>Alle Categorieën</li><li>Zuurstofconcentrator</li><li>Draagbare Zuurstofconcentrator</li><li>Filters</li><li>Huren</li><li>Supplies</li><li>Contact</li>
</ul></nav>

<section class="hero" role="img" aria-label="Photo of a woman reading a book in an armchair while using an oxygen cannula">
  <svg class="hero-cut" viewBox="0 0 1200 120" preserveAspectRatio="none"><polygon points="0,120 1200,0 1200,120" fill="#fff"/></svg>
  <div class="hero-text"><h1>Unsere Produkte</h1><span class="btn-orange">Vraag een offerte aan</span></div>
</section>

<div class="sec-title"><small>Produkte</small><h2>Unsere <em>Produkte</em></h2></div>

<aside class="sidebar">
  <div class="sb-head">FILTER <span class="clear"><b>✕</b> Klar</span></div>
  <div class="sb-sec">
    <div class="sb-title">PREIS <i class="minus"></i></div>
    <div class="range"><i style="left:-4px"></i><i style="right:-4px"></i></div>
    <div class="prices">€ <span>1</span> € <span>645</span></div>
  </div>
  <div class="sb-sec" style="padding-bottom:22px">
    <div class="sb-title">BRANDS <i class="minus"></i></div>
    <div class="brands"><span>Veltmann</span><span>Careline</span><span>Aerion</span><span>Gasko</span><span>Luvra</span><span>Brevo</span></div>
  </div>
  <div>
    <div class="sb-title" style="height:48px;align-items:flex-end;padding-bottom:6px">TAGS <i class="minus"></i></div>
    <ul class="tags"><i class="thumb"></i>
      <li>Schrankfilter Calmair</li><li>Kanülen und Schläuche</li><li>Calmair</li><li>Calmair-Handbuch</li><li>Filter Calmair</li><li>Filter Calmair</li><li>Durchflussmesser Calmair</li><li>Sauerstoffanreicherung</li><li>oxygen enrichment</li><li>Clearpath</li>
    </ul>
  </div>
</aside>

<div class="toolbar">
  <div class="view"><svg width="14" height="14" viewBox="0 0 14 14" fill="#0a6cb5"><circle cx="2" cy="2" r="1.6"/><circle cx="7" cy="2" r="1.6"/><circle cx="12" cy="2" r="1.6"/><circle cx="2" cy="7" r="1.6"/><circle cx="7" cy="7" r="1.6"/><circle cx="12" cy="7" r="1.6"/><circle cx="2" cy="12" r="1.6"/><circle cx="7" cy="12" r="1.6"/><circle cx="12" cy="12" r="1.6"/></svg><svg width="16" height="14" viewBox="0 0 16 14" fill="#0a6cb5"><rect y="1" width="3" height="2"/><rect x="4" y="1" width="12" height="2"/><rect y="6" width="3" height="2"/><rect x="4" y="6" width="12" height="2"/><rect y="11" width="3" height="2"/><rect x="4" y="11" width="12" height="2"/></svg></div>
  <div class="compare"><svg class="ico" style="width:14px;height:14px" viewBox="0 0 24 24"><path d="M4 4h10v4M20 20H10v-4M4 4v16h6M20 20V4h-6"/></svg>Produktvergleich</div>
  <span class="tb-btn">Sortieren nach:</span>
  <span class="tb-sel" style="width:119px">Standard <span>⌄</span></span>
  <span class="tb-btn" style="margin-left:0">Anzeigen</span>
  <span class="tb-sel" style="width:56px;margin-right:0">14 <span>⌄</span></span>
</div>

<div class="grid">
  <article class="card"><div class="photo" role="img" aria-label="White stationary oxygen concentrator"></div><h3>Noordlicht</h3><p class="price">€1.526,00</p><div class="stars"><svg><use href="#star"/></svg><svg><use href="#star"/></svg><svg><use href="#star"/></svg><svg><use href="#star"/></svg><svg><use href="#star"/></svg></div></article>
  <article class="card"><div class="photo alt" role="img" aria-label="Grey 10 litre oxygen concentrator"></div><h3>Orbit 10 Liter zuurstofconcentrator</h3><p class="price">€1.084,55</p><div class="stars"><svg><use href="#star"/></svg><svg><use href="#star"/></svg><svg><use href="#star"/></svg><svg><use href="#star"/></svg><svg><use href="#star"/></svg></div></article>
  <article class="card"><div class="photo" role="img" aria-label="Dark grey 10 litre oxygen concentrator"></div><h3>Tempo 10 Liter zuurstofconcentrator</h3><p class="price">€1.084,55</p><div class="stars"><svg><use href="#star"/></svg><svg><use href="#star"/></svg><svg><use href="#star"/></svg><svg><use href="#star"/></svg><svg><use href="#star"/></svg></div></article>
  <article class="card"><div class="photo" role="img" aria-label="Portable oxygen concentrator on a trolley cart"></div><h3>Brevo T2|T4 | Stroll 4 trolly |cart</h3><p class="price">€147.15</p><div class="stars"><svg><use href="#star"/></svg><svg><use href="#star"/></svg><svg><use href="#star"/></svg><svg><use href="#star"/></svg><svg><use href="#star"/></svg></div></article>
  <article class="card"><div class="photo alt" role="img" aria-label="White compact oxygen concentrator on wheels"></div><h3>Halvorn Serene 5</h3><p class="price">€1.084,55</p><div class="stars"><svg><use href="#star"/></svg><svg><use href="#star"/></svg><svg><use href="#star"/></svg><svg><use href="#star"/></svg><svg><use href="#star"/></svg></div></article>
  <article class="card"><div class="photo" role="img" aria-label="Portable oxygen concentrator with large battery"></div><h3>Brevo Stroll 4 16 Cell ( grote batterij)</h3><p class="price">€1.084,55</p><div class="stars"><svg><use href="#star"/></svg><svg><use href="#star"/></svg><svg><use href="#star"/></svg><svg><use href="#star"/></svg><svg><use href="#star"/></svg></div></article>
  <article class="card"><div class="photo" role="img" aria-label="White stationary oxygen concentrator"></div><h3>Noordlicht</h3><p class="price">€1.526,00</p><div class="stars"><svg><use href="#star"/></svg><svg><use href="#star"/></svg><svg><use href="#star"/></svg><svg><use href="#star"/></svg><svg><use href="#star"/></svg></div></article>
  <article class="card"><div class="photo alt" role="img" aria-label="Black compact oxygen concentrator"></div><h3>Oxygen concentrato Basis 300</h3><p class="price">€801.15</p><div class="stars"><svg><use href="#star"/></svg><svg><use href="#star"/></svg><svg><use href="#star"/></svg><svg><use href="#star"/></svg><svg><use href="#star"/></svg></div></article>
  <article class="card"><div class="photo" role="img" aria-label="Dark grey 10 litre oxygen concentrator"></div><h3>Tempo 10 Liter zuurstofconcentrator</h3><p class="price">€1.084,55</p><div class="stars"><svg><use href="#star"/></svg><svg><use href="#star"/></svg><svg><use href="#star"/></svg><svg><use href="#star"/></svg><svg><use href="#star"/></svg></div></article>
</div>

<div class="pager">
  <span class="prev"><svg width="10" height="10" viewBox="0 0 10 10"><path d="M7 1L3 5l4 4" stroke="#fff" stroke-width="1.8" fill="none"/></svg></span>
  <span>1</span><span>2</span><span>3</span><span>4</span><span>5</span><span>6</span><span>7</span><span>8</span>
  <span class="next"><svg width="10" height="10" viewBox="0 0 10 10"><path d="M3 1l4 4-4 4" stroke="#fff" stroke-width="1.8" fill="none"/></svg></span>
</div>

<div class="pay-band"></div>
<section class="pay">
  <h2>Veilige Betalingen Mogelijk <em>Gemaakt Door Paydrift</em></h2>
  <div class="cards"><span>Paynest</span><span>Cardora</span><span>Vexa</span><span>Amerion Pay</span><span>Amion</span><span>iBetaal</span></div>
</section>

<footer class="footer">
  <div class="fcol" style="width:239px"><h4>Snelle Links</h4><ul><li>Over ons</li><li>Verzending</li><li>Privacy Policy</li><li>Algemene voorwaarden</li><li>Zakelijk</li></ul></div>
  <div class="fcol" style="width:217px"><h4>Klantnservice</h4><ul><li>Contact</li><li>Garantie en Service</li><li>Retourneren</li><li>Site Map</li><li>Merken</li></ul></div>
  <div class="fcol" style="width:224px"><h4>Mijn account</h4><ul><li>Mijn account</li><li>Bestel historie</li></ul><h4 style="margin-top:12px">Documentatie</h4><ul><li>Veel gestelde vragen</li></ul></div>
  <div class="fcol" style="width:240px">
    <div class="brand" style="font-size:44px;padding-top:12px"><i></i>luvra</div>
    <div class="finfo"><svg class="ico" style="stroke:#0a6cb5;width:32px;height:32px" viewBox="0 0 24 24"><path d="M12 21s-6-6-6-11a6 6 0 0 1 12 0c0 5-6 11-6 11z"/><circle cx="12" cy="10" r="2"/></svg><div><b>Bedrijfs gegevens</b><br>Btw nummer NL000111222B01<br>K.V.K. 123 45678</div></div>
    <div class="finfo"><svg class="ico" style="stroke:#0a6cb5;width:32px;height:32px" viewBox="0 0 24 24"><path d="M5 3h4l2 5-3 2a11 11 0 0 0 6 6l2-3 5 2v4a2 2 0 0 1-2 2A17 17 0 0 1 3 5a2 2 0 0 1 2-2z"/></svg><div><b>Telefoon van uit België en</b><br>buitenland +31701234567</div></div>
  </div>
</footer>

<div class="bottom">© 2025, Luvra BV, Alle Rechten Voorbehouden</div>
</body>
</html>
```